Velk Partners Building Business Cards

We need a business card that reflects our business as "Solar Experts" in San Diego. Browse our website www.velkpartners.example our License needs to be displayed as "CSLB# 3867140" our phone number is (619) 555-0187

Save thousands on your electric bills and increase the value of your home while helping to protect the environment. Our solar installation experts will help you design the system that's right for you, using only the highest quality equipment that will look great and give you ideal performance. Our goal is to make you energy independent, and get your electric bill to 0.

Paul Osterby
(619) 555-0187
paul@velkpartners.example

Target Market(s)

Home owners in san diego looking for solar

Industry/Entity Type

Solar Energy

Contact Information for Business Card

Paul Osterby
(619) 555-0187
paul@velkpartners.example

Font styles to use
Other font styles liked:
• Use our logo font

Requirements
Must have
• License needs to be displayed as "CSLB# 3867140" our phone number is (619) 555-0187
Nice to have
• Real images of rooftop home solar in san diego
Should not have
• our business address

```html
<!DOCTYPE html>
<html lang="en">
<head>
<meta charset="utf-8">
<title>Velk Partners Building – Business Cards</title>
<link rel="stylesheet" href="https://fonts.googleapis.com/css2?family=Roboto:wght@400;700&display=swap">
<style>
  :root {
    --brand-blue: #1e5fae;
    --brand-blue-deep: #17498b;
    --sun-yellow: #f5c21b;
    --paper: #ffffff;
    --paper-shade: #f1f2f4;
    --backdrop: #e6e7ea;
    --ink-white: #ffffff;
  }
  * { box-sizing: border-box; margin: 0; padding: 0; }
  html, body { width: 1200px; height: 1000px; overflow: hidden; }
  body {
    background: var(--backdrop);
    font-family: "Roboto", Arial, sans-serif;
    position: relative;
  }
  .card {
    position: absolute;
    left: 220px;
    width: 760px;
    height: 434px;
    border-radius: 4px;
    overflow: hidden;
    box-shadow: 0 6px 18px rgba(0,0,0,0.18);
  }
  .card--front { top: 50px; display: flex; }
  .card--back {
    top: 516px;
    background: linear-gradient(160deg, var(--paper) 55%, var(--paper-shade));
    display: flex;
    align-items: center;
    justify-content: center;
  }

  /* Front: brand panel */
  .brand-panel {
    width: 260px;
    background: linear-gradient(180deg, var(--paper), var(--paper-shade));
    display: flex;
    align-items: center;
    justify-content: center;
    padding: 0 24px;
  }
  .brand-name {
    display: flex;
    align-items: center;
    gap: 12px;
    color: var(--brand-blue);
    font-weight: 700;
    line-height: 1.1;
  }
  .brand-name--small { font-size: 28px; }
  .brand-name--large { font-size: 50px; gap: 18px; }
  .brand-dot {
    flex: none;
    border-radius: 50%;
    background: var(--sun-yellow);
  }
  .brand-name--small .brand-dot { width: 20px; height: 20px; }
  .brand-name--large .brand-dot { width: 34px; height: 34px; }

  /* Front: contact panel */
  .contact-panel {
    position: relative;
    flex: 1;
    background: linear-gradient(135deg, var(--brand-blue) 0%, var(--brand-blue-deep) 100%);
    color: var(--ink-white);
    padding: 0 0 0 70px;
    display: flex;
    flex-direction: column;
    justify-content: center;
  }
  .contact-panel__notch {
    position: absolute;
    left: 0;
    top: 236px;
    width: 14px;
    height: 24px;
    background: var(--paper);
    clip-path: polygon(0 0, 100% 50%, 0 100%);
  }
  .person-name {
    font-size: 36px;
    font-weight: 700;
    letter-spacing: 0.5px;
    margin-bottom: 26px;
  }
  .person-name__last { color: var(--sun-yellow); }
  .contact-list { list-style: none; font-size: 19px; }
  .contact-list li {
    display: flex;
    align-items: center;
    gap: 14px;
    margin-bottom: 12px;
  }
  .contact-list svg { width: 18px; height: 18px; flex: none; }
  .highlight { color: var(--sun-yellow); }
  .license-line {
    color: var(--sun-yellow);
    font-size: 18px;
    margin-top: 6px;
    padding-left: 32px;
  }
</style>
</head>
<body>

  <section class="card card--front" aria-label="Business card front">
    <div class="brand-panel">
      <div class="brand-name brand-name--small">
        <span>Velk Partners<br>Building</span>
        <span class="brand-dot"></span>
      </div>
    </div>
    <div class="contact-panel">
      <span class="contact-panel__notch"></span>
      <h1 class="person-name">PAUL <span class="person-name__last">OSTERBY</span></h1>
      <ul class="contact-list">
        <li>
          <svg viewBox="0 0 18 18" fill="none" stroke="#fff" stroke-width="1.4"><rect x="5" y="1.5" width="8" height="15" rx="1.5"/><line x1="8" y1="14" x2="10" y2="14"/></svg>
          <span>(619) 555-0187</span>
        </li>
        <li>
          <svg viewBox="0 0 18 18" fill="none" stroke="#fff" stroke-width="1.4"><rect x="1.5" y="4" width="15" height="10"/><polyline points="1.5,4 9,10 16.5,4"/></svg>
          <span>paul@velkpartners.example</span>
        </li>
        <li>
          <svg viewBox="0 0 18 18" fill="none" stroke="#fff" stroke-width="1.4"><circle cx="9" cy="9" r="7.5"/><ellipse cx="9" cy="9" rx="3.2" ry="7.5"/><line x1="1.5" y1="9" x2="16.5" y2="9"/></svg>
          <span>www.<span class="highlight">velkpartners</span>.example</span>
        </li>
      </ul>
      <p class="license-line">License-"CSLB# 3867140"</p>
    </div>
  </section>

  <section class="card card--back" aria-label="Business card back">
    <div class="brand-name brand-name--large">
      <span>Velk Partners Building</span>
      <span class="brand-dot"></span>
    </div>
  </section>

</body>
</html>
```